Electric mountain bike tours nz

We are an Electric Mountain bike tour company in New Zealand. We will be offering bike rental and guided tours around the Nelson region in New Zealand. I want our website to represent both Mountain biking and New Zealand with the colours layout and features. We want tabs for the following:
-1 about us
-2 what we offer
-3 bookings/contact
Under the about us tab will be who we are as a a company. I want the ability to add videos to each of these tabs as we move foward with videos of the tracks we will be riding. I want the website to be editable so I can add and remove videos/photos myself. Also "our bikes" will be under this tab.
Under the what we offer tab will be
-1 bike rental and pricing
-2 guided tours and pricing
-3 recommended package deals.
I want to able to put the tracks under the guided tours tab and select beginner/ intermediate/advanced and have the tracks in each of the following to match the rider level. Also to be able to have a small video of the track would be great in this section.
Bookings and contact tab
(Further information for this tab to be updated soon)
Coded - Design and coding required
1 page
- Silver ferns, kiwi, mountains

```html
<!DOCTYPE html>
<html lang="en">
<head>
<meta charset="utf-8">
<title>Ridgeline – Electric Mountain Bike Tours</title>
<link rel="stylesheet" href="https://fonts.googleapis.com/css2?family=Montserrat:wght@400;500;600;700;800&family=Open+Sans:ital,wght@0,400;0,600;1,400&display=swap">
<style>
:root{
  --ink:#1a1a1a;
  --text:#333333;
  --white:#ffffff;
  --grey:#ececec;
  --line:#dddddd;
  --black:#000000;
  --red:#d81f26;
  --footer:#141414;
  --ph-light:#e4e4e4;
  --ph-mid:#cfcfcf;
  --ph-edge:#c4c4c4;
}
*{margin:0;padding:0;box-sizing:border-box}
html,body{width:1200px;height:4489px;overflow:hidden}
body{position:relative;background:var(--white);font-family:"Open Sans",Arial,sans-serif;color:var(--text)}
.abs{position:absolute}
.head{font-family:"Montserrat",Arial,sans-serif;font-weight:800;color:var(--ink);letter-spacing:.5px}
.small{font-size:10.5px;line-height:17px;color:var(--text)}
.ph{position:absolute}
.ph-object{background:linear-gradient(180deg,var(--ph-light),var(--ph-mid));border:1px solid var(--ph-edge);border-radius:4px}
.ph-kiwi{background:linear-gradient(180deg,#8a7458,#6a5640);border-radius:4px}
.ph-kiwi.grey{background:linear-gradient(180deg,#8a8a8a,#6a6a6a)}

/* header */
.topbar{left:0;top:0;width:1200px;height:115px;background:var(--white);z-index:3}
.brand{left:150px;top:4px;width:124px;height:124px;border-radius:50%;background:var(--white);z-index:4;display:flex;align-items:center;justify-content:center;font-family:"Montserrat",sans-serif;font-weight:800;font-size:17px;color:var(--ink);letter-spacing:1px}
.phone{left:818px;top:24px;font-family:"Montserrat",sans-serif;font-size:21px;color:var(--ink);display:flex;align-items:center;gap:8px;z-index:4}
.nav{top:72px;left:474px;display:flex;gap:40px;font-family:"Montserrat",sans-serif;font-weight:600;font-size:13px;color:var(--ink);z-index:4}

/* hero */
.hero{left:0;top:115px;width:1200px;height:725px;background:linear-gradient(160deg,#3a4d5c 0%,#5b6b4a 40%,#6e6a34 70%,#4a4522 100%)}
.hero-title{left:160px;top:345px;width:520px;font-family:"Montserrat",sans-serif;font-weight:700;font-size:33px;line-height:40px;color:var(--white);z-index:2}

.btn{display:inline-block;font-family:"Montserrat",sans-serif;font-weight:700;font-size:11px;border-radius:20px;text-align:center}
.lead{font-size:13px;line-height:22px}

/* pricing */
.card{top:2425px;width:280px;height:515px;border:1px solid var(--line);background:var(--white)}
.card.featured{border:3px solid var(--black)}
.card-top{position:absolute;left:0;top:0;width:100%;height:155px}
.badge{position:absolute;left:50%;top:22px;width:100px;height:100px;margin-left:-50px;border-radius:50%;border:4px dashed var(--white);display:flex;flex-direction:column;align-items:center;justify-content:center;color:var(--white);font-family:"Montserrat",sans-serif}
.badge .tier{font-size:8px;font-weight:600;letter-spacing:1px}
.badge .price{font-size:28px;font-weight:800}
.features{position:absolute;top:172px;left:12px;right:12px;list-style:none}
.features li{font-size:10px;text-align:center;height:33.5px;line-height:33px;border-bottom:1px solid var(--line);color:var(--text)}
.order{position:absolute;left:50%;bottom:22px;margin-left:-52px;width:104px;height:28px;line-height:24px;border:2px solid var(--ink);color:var(--ink);font-size:10px}
.bike-ic{top:2335px;width:140px;height:80px}

/* news */
.news-img{top:3785px;width:268px;height:172px}
.news-title{top:3975px;width:268px;font-family:"Montserrat",sans-serif;font-weight:600;font-size:15px;line-height:20px;color:var(--ink)}
.news-text{top:4030px;width:268px}
.news-date{top:4140px;font-family:"Montserrat",sans-serif;font-weight:700;font-size:13px;color:var(--ink)}

/* footer */
.footer{left:0;top:4232px;width:1200px;height:257px;background:var(--footer);color:var(--white)}
.fbrand{left:540px;top:10px;width:120px;height:100px;display:flex;align-items:center;justify-content:center;font-family:"Montserrat",sans-serif;font-weight:800;font-size:17px;letter-spacing:1px}
.fnav{top:136px;left:0;width:1200px;display:flex;justify-content:center;gap:40px;font-family:"Montserrat",sans-serif;font-weight:600;font-size:12px}
.copy{top:168px;left:0;width:1200px;text-align:center;font-size:10px;color:#bbbbbb}
.social{top:194px;left:0;width:1200px;display:flex;justify-content:center;gap:10px}
.social span{width:22px;height:22px;border:1.5px solid var(--white);border-radius:50%}
</style>
</head>
<body>

<!-- header -->
<div class="abs topbar"></div>
<div class="abs brand">RIDGELINE</div>
<div class="abs phone">
  <svg width="18" height="18" viewBox="0 0 24 24"><path fill="#1a1a1a" d="M6.6 10.8a15.1 15.1 0 0 0 6.6 6.6l2.2-2.2c.3-.3.7-.4 1-.2 1.1.4 2.3.6 3.6.6.6 0 1 .4 1 1V20c0 .6-.4 1-1 1A17 17 0 0 1 3 4c0-.6.4-1 1-1h3.5c.6 0 1 .4 1 1 0 1.3.2 2.5.6 3.6.1.3 0 .7-.2 1z"/></svg>
  Call Us : 0412 555 018
</div>
<nav class="abs nav"><span>HOME</span><span>ABOUT US</span><span>WHAT WE OFFER</span><span>BOOKINGS</span><span>CONTACT US</span></nav>

<!-- hero -->
<div class="ph hero" role="img" aria-label="Red electric mountain bike parked on a wooden deck above a tussock-covered valley"></div>
<svg class="abs" style="left:0;top:660px;z-index:1" width="1200" height="182"><polygon points="0,20 720,150 1200,95 1200,182 0,182" fill="#ffffff"/></svg>
<h1 class="abs hero-title">Sed ut perspiciatis unde omnis iste natus error sit voluptatem accusantium doloremqueve</h1>

<!-- about -->
<h2 class="abs head" style="left:160px;top:862px;font-size:31px">ABOUT US</h2>
<p class="abs lead" style="left:160px;top:922px;width:440px">Sed ut perspiciatis unde omnis iste natus error sit voluptatem accusa ntium doloremque laudantium, totam rem aperiam, eaque ipsa quae ab illo inventore veritatis et quasi architecto beatae vitae dicta sunt</p>
<p class="abs small" style="left:160px;top:1022px;width:215px">Sed ut perspiciatis unde omnis iste natus err or sit voluptatem accusantium dolore mque laudantium, totam rem aperiam, eaque ipsa quae ab illo inventore veritatis et quasi arc hite cto beatae vitae dictasit explic abo enim ilonpsam voluptatemla voluptas sit aspe rnatur aut odit au</p>
<p class="abs small" style="left:402px;top:1022px;width:215px">Sed ut perspiciatis unde omnis iste natus err or sit voluptatem accusantium dolore mque laudantium, totam rem aperiam, eaque ipsa quae ab illo inventore veritatis et quasi arc hite cto beatae vitae dictasit explic abo enim ilonpsam voluptatemla voluptas sit aspe rnatur aut odit au</p>
<span class="abs btn" style="left:160px;top:1193px;width:102px;height:32px;line-height:32px;background:var(--ink);color:var(--white)">READ MORE</span>
<div class="ph ph-object" style="left:660px;top:880px;width:515px;height:300px" role="img" aria-label="Black full-suspension electric mountain bike, side view"></div>
<div class="ph ph-kiwi" style="left:958px;top:1242px;width:90px;height:100px;z-index:1" role="img" aria-label="Kiwi bird"></div>

<!-- what we do -->
<svg class="abs" style="left:0;top:1262px" width="1200" height="850"><polygon points="0,40 420,0 1200,80 1200,770 430,815 0,780" fill="#ececec"/></svg>
<h2 class="abs head" style="left:160px;top:1450px;font-size:31px">WHAT WE DO</h2>
<p class="abs" style="left:160px;top:1528px;width:345px;font-size:12.5px;line-height:20px;font-style:italic">Sed ut perspiciatis unde omnis iste natus error sit volupte m accusantium doloremque laudantium, totam rem aperi am, eaque ipsa quae ab illo inventore veritat is et qasuiarchte beatae vitae dicesque ipsa quae ab illo inventse veritis, suab illo inventore veritat is eleuant.</p>
<p class="abs small" style="left:555px;top:1450px;width:487px;line-height:19px">Sed ut perspiciatis unde omnis iste natus err or sit voluptatem accusantium dolore mque lau dtun antium, totam rem aperiam, eaque ipsa quae ab illo inventore veritatis et quasi arc hite cto beatae vitae dictasit explic abo enim ilonpsam voluptatemla voluptas sit aspe rnatur aut odit autend ut perspiciatis unde omnis iste natus err or sit voluptatem accusantium dolore emque lau dtnantium, totam rem aperiam, eaque ipsa quae ab illo inventore veritatis et qu asi arc hite cto beatae vitae dictasit explic abo enim ilonpsam voluptatemla voluptas sit aspe rnatur aut odit autend ut perspi ciatis unde omnis iste natperspiciatis unde omnis iste natus err or sit voluptatem accusantium dolore mque lau dtnantium, totam rem aperiam, eaque ipsa quae ab illo inventore veritatis et qu asi arc hite cto beatae vitae dictasit explic abo enim</p>
<div class="ph" style="left:160px;top:1675px;width:370px;height:262px;background:linear-gradient(160deg,#7a8a4a,#5a5236 60%,#3f4a28)" role="img" aria-label="Brown kiwi foraging on mossy forest floor"></div>
<div class="ph" style="left:555px;top:1675px;width:487px;height:262px;background:linear-gradient(180deg,#c9d4de 0%,#6f8a9c 40%,#3a4330 75%,#2a2a20)" role="img" aria-label="Electric mountain bike on a ridge overlooking the sea at dusk"></div>

<!-- pricing -->
<div class="ph ph-kiwi" style="left:195px;top:2140px;width:120px;height:110px" role="img" aria-label="Kiwi bird"></div>
<h2 class="abs head" style="left:0;width:1200px;top:2208px;font-size:31px;text-align:center">PRICING PLANS</h2>
<p class="abs small" style="left:320px;top:2262px;width:560px;text-align:center;font-size:10px">Sed ut perspiciatis unde omnis iste natus error sit voluptatem accusantium doloremque laudantium, totam rem aperiam, eaque ipsa quae ab illo inventore veritatis et quasi architecto beatae vitae dicta sunt explc</p>

<div class="ph ph-object bike-ic" style="left:233px" role="img" aria-label="Mountain bike"></div>
<div class="ph ph-object bike-ic" style="left:532px" role="img" aria-label="Mountain bike"></div>
<div class="ph ph-object bike-ic" style="left:830px" role="img" aria-label="Mountain bike"></div>
<div class="abs" style="left:652px;top:2326px;width:56px;height:56px;border-radius:50%;background:var(--red);color:var(--white);font-family:Montserrat,sans-serif;font-weight:700;font-size:8px;display:flex;align-items:center;justify-content:center;text-align:center;line-height:10px;z-index:1">BEST<br>OFFER</div>

<div class="abs card" style="left:163px">
  <svg class="card-top" viewBox="0 0 280 155" preserveAspectRatio="none"><polygon points="0,0 280,0 280,120 0,155" fill="#2e2e2e"/></svg>
  <div class="badge"><span class="tier">BASIC</span><span class="price">$299</span></div>
  <ul class="features"><li>Sed ut perspiciatisde</li><li>Omnis iste natus error sit vol</li><li>Totem accusantium dolore</li><li>Mque laudccusantiumantium</li><li>Aem reccusantium dolem</li><li>Accusantium dolore</li><li>Mque laudccusantium</li></ul>
  <span class="btn order">ORDER NOW</span>
</div>
<div class="abs card featured" style="left:462px">
  <svg class="card-top" viewBox="0 0 280 155" preserveAspectRatio="none"><polygon points="0,0 280,0 280,155 0,120" fill="#000000"/></svg>
  <div class="badge"><span class="tier">STANDARD</span><span class="price">$599</span></div>
  <ul class="features"><li>Sed ut perspiciatisde</li><li>Omnis iste natus error sit vol</li><li>Totem accusantium dolore</li><li>Mque laudccusantiumantium</li><li>Aem reccusantium dolem</li><li>Accusantium dolore</li><li>Mque laudccusantium</li><li>Accusantium dolore</li></ul>
  <span class="btn order">ORDER NOW</span>
</div>
<div class="abs card" style="left:760px">
  <svg class="card-top" viewBox="0 0 280 155" preserveAspectRatio="none"><polygon points="0,0 280,0 280,120 0,155" fill="#2e2e2e"/></svg>
  <div class="badge"><span class="tier">PLATINUM</span><span class="price">$699</span></div>
  <ul class="features"><li>Sed ut perspiciatisde</li><li>Omnis iste natus error sit vol</li><li>Totem accusantium dolore</li><li>Mque laudccusantiumantium</li><li>Aem reccusantium dolem</li><li>Accusantium dolore</li><li>Mque laudccusantium</li><li>Accusantium dolore</li></ul>
  <span class="btn order">ORDER NOW</span>
</div>

<!-- video -->
<svg class="abs" style="left:0;top:2995px" width="1200" height="740" role="img" aria-label="Faded grassy hillside backdrop">
  <defs><linearGradient id="hill" x1="0" y1="0" x2="0" y2="1"><stop offset="0" stop-color="#e6e8e4"/><stop offset="1" stop-color="#c9cdc3"/></linearGradient></defs>
  <polygon points="0,55 420,0 1200,65 1200,590 720,740 0,560" fill="url(#hill)"/>
</svg>
<div class="ph" style="left:160px;top:3210px;width:485px;height:290px;background:linear-gradient(180deg,#6f93c4 0%,#b9cbe0 35%,#f2f4f6 50%,#6a6f66 75%,#3d3a30)" role="img" aria-label="Rider with mountain bike in front of snowy alpine peaks"></div>
<svg class="abs" style="left:365px;top:3320px" width="70" height="70"><circle cx="35" cy="35" r="33" fill="#111111" stroke="#ffffff" stroke-width="3"/><polygon points="27,20 27,50 51,35" fill="#ffffff"/></svg>
<div class="ph ph-object" style="left:32px;top:3418px;width:285px;height:150px" role="img" aria-label="Grey electric mountain bike, side view"></div>
<h2 class="abs head" style="left:715px;top:3222px;font-size:31px">OUR VIDEO</h2>
<p class="abs small" style="left:715px;top:3285px;width:285px;line-height:18px">Sed ut perspiciatis unde omnis iste natus err or volup tatem accusantium dolore mque lau dtunantium, totam rem aperiam, eaque ipsa quae ab illo inventore veritatis et quasi arc hite cto beatae vitae dictasit explic abo enim ilonpsam voluptatemla voluptas sit aspe rnatur aut odit autend ut perspiciatis unde omnis iste natus err or sit voluptatem accusantium dolore mque lau dtnantium, totam rem aperiam, eaque ipsa quae ab illo inventore ver</p>
<div class="ph ph-kiwi grey" style="left:1005px;top:3540px;width:95px;height:105px" role="img" aria-label="Kiwi bird"></div>

<!-- news -->
<h2 class="abs head" style="left:160px;top:3705px;font-size:31px">LATEST NEWS</h2>
<div class="ph news-img" style="left:160px;background:linear-gradient(160deg,#c9d5e2,#8a7a6a 60%,#4a3a30)" role="img" aria-label="Rider in red jacket on a rocky mountain trail"></div>
<div class="ph news-img" style="left:465px;background:linear-gradient(180deg,#b7b56a 0%,#6a7a3a 45%,#2e3a1c 100%)" role="img" aria-label="Rider on a forest trail with sun through trees"></div>
<div class="ph news-img" style="left:770px;background:linear-gradient(180deg,#c9d4de 0%,#6f8a9c 40%,#3a4330 75%,#2a2a20)" role="img" aria-label="Electric bike parked above the coast"></div>

<h3 class="abs news-title" style="left:160px">Sed ut perspiciatis unde omniste natusrror sit voluptat accusn.</h3>
<h3 class="abs news-title" style="left:465px">Sed ut perspiciatis unde nis iste natusrror sit voluptat accusn.</h3>
<h3 class="abs news-title" style="left:770px">Sed ut perspiciatis unde omnis iste natusrror sit voluptat accusn.</h3>
<p class="abs small news-text" style="left:160px">Sed ut perspiciatis unde omnis iste natus err orsit atem accusantium dolore mque laudtunantium rem aperiam, eaque ipsa quae ab illo inventoreet quasi arc hite beatae vitae dictasn.</p>
<p class="abs small news-text" style="left:465px">Sed ut perspiciatis unde omnis iste natus err orsit atem accusantium dolore mque laudtunantium rem aperiam, eaque ipsa quae ab illo inventoreet quasi arc hite beatae vitae dictasn.</p>
<p class="abs small news-text" style="left:770px">Sed ut perspiciatis unde omnis iste natus err orsit atem accusantium dolore mque laudtunantium rem aperiam, eaque ipsa quae ab illo inventoreet quasi arc hite beatae vitae dictasn.</p>
<span class="abs news-date" style="left:160px">—— 25 July, 2018</span>
<span class="abs news-date" style="left:465px">—— 25 July, 2018</span>
<span class="abs news-date" style="left:770px">—— 25 July, 2018</span>

<!-- footer -->
<footer class="abs footer">
  <div class="abs fbrand">RIDGELINE</div>
  <nav class="abs fnav"><span>HOME</span><span>ABOUT US</span><span>WHAT WE OFFER</span><span>BOOKINGS</span><span>CONTACT US</span></nav>
  <p class="abs copy">©2018 All Rights Reserved. Privacy policy</p>
  <div class="abs social"><span></span><span></span><span></span><span></span><span></span><span></span></div>
</footer>

</body>
</html>
```